Lanterns After Rain ---Marla Quintbury; EP cover

I am a pop artist and need my name and title of the EP designed onto professional pictures.(Lanterns After Rain---Marla Quintbury) I am open to color for lettering and other design elements. I'd really like something that compliments the photo(s)! To get a feel for what I'm looking for-- reference past CD covers from pop artists like- Selene Trovato, Daisy Pemberton, Noor Halvik, etc. Can't wait to see what you design!

Font styles to use
Serif
Sans Serif
Decorative
Script

Requirements
Must have
• I would like very little alteration to the pictures other than fitting pictures to the dimensions required for the CD cover. Some softening or a little bit of blurring to the picture is ok.
Nice to have
• My initial thought was to keep everything grayscale to match the photos, but if you feel so inspired--create!
Should not have
• No flashy lettering

```html
<!DOCTYPE html>
<html lang="en">
<head>
<meta charset="utf-8">
<title>Lanterns After Rain — Marla Quintbury</title>
<link rel="stylesheet" href="https://fonts.googleapis.com/css2?family=Inter:wght@300;900&family=Playfair+Display:wght@500&display=swap">
<style>
  :root {
    --page-bg: #e4e8ee;
    --photo-deep: #3a2a22;
    --photo-amber: #a35a22;
    --photo-copper: #c9763a;
    --photo-cream: #f1d4b4;
    --photo-glow: #fbe9d2;
    --type-light: #ffffff;
    --type-accent: #f2e21c;
  }
  * { margin: 0; padding: 0; box-sizing: border-box; }
  html, body {
    width: 1200px;
    height: 900px;
    overflow: hidden;
    background: var(--page-bg);
  }
  .cover {
    position: absolute;
    left: 200px;
    top: 50px;
    width: 800px;
    height: 800px;
    overflow: hidden;
  }
  .cover-photo {
    position: absolute;
    inset: 0;
    background:
      radial-gradient(ellipse 55% 70% at 88% 35%, var(--photo-glow) 0%, var(--photo-cream) 35%, rgba(241,212,180,0) 70%),
      radial-gradient(ellipse 40% 60% at 40% 45%, rgba(58,42,34,0.95) 0%, rgba(58,42,34,0) 75%),
      linear-gradient(100deg, var(--photo-amber) 0%, var(--photo-copper) 25%, var(--photo-deep) 45%, var(--photo-copper) 62%, var(--photo-cream) 85%);
  }
  .artist-name {
    position: absolute;
    left: 150px;
    top: 395px;
    font-family: "Inter", sans-serif;
    font-size: 27px;
    letter-spacing: 0.04em;
    color: var(--type-light);
    text-transform: uppercase;
    white-space: nowrap;
  }
  .artist-first { font-weight: 900; }
  .artist-last { font-weight: 300; }
  .ep-title {
    position: absolute;
    left: 145px;
    top: 425px;
    font-family: "Playfair Display", serif;
    font-weight: 500;
    color: var(--type-light);
    line-height: 0.78;
    font-size: 96px;
    text-shadow: 2px 3px 6px rgba(0,0,0,0.25);
  }
  .ep-title .line { display: block; white-space: nowrap; }
  .ep-title .line-accent {
    color: var(--type-accent);
    padding-left: 40px;
  }
  .ep-title .initial {
    font-size: 150px;
    vertical-align: -0.18em;
  }
  .ep-title .line-last { padding-left: 60px; }
</style>
</head>
<body>
  <main class="cover">
    <div class="cover-photo" role="img" aria-label="Warm amber-toned close-up portrait photograph of the artist with loose blonde hair across the frame"></div>
    <p class="artist-name"><span class="artist-first">Marla</span> <span class="artist-last">Quintbury</span></p>
    <h1 class="ep-title">
      <span class="line">Lanterns</span>
      <span class="line line-accent"><span class="initial">A</span>fter</span>
      <span class="line line-last">Rain</span>
    </h1>
  </main>
</body>
</html>
```